Business card for medical clinic

I need an upmarket, modern medical/health business card for my clinic

Contact Information for Business Card

name, address, email, qr code

```html
<!DOCTYPE html>
<html lang="en">
<head>
<meta charset="utf-8">
<title>Meridel Health Clinic – Business Card</title>
<link rel="stylesheet" href="https://fonts.googleapis.com/css2?family=Poppins:wght@300;400;500;600&display=swap">
<style>
  :root {
    --stage: #232323;
    --card-dark: #1f1f22;
    --card-band: #29292d;
    --brand-blue: #22aae3;
    --ink-light: #f2f2f2;
    --ink-muted: #cfd2d6;
    --icon-blue: #2aa8e0;
  }
  * { margin: 0; padding: 0; box-sizing: border-box; }
  html, body {
    width: 1200px; height: 780px; overflow: hidden;
    background: var(--stage);
    font-family: "Poppins", sans-serif;
  }
  .sheet {
    width: 1200px; height: 780px;
    display: flex; align-items: center; justify-content: center; gap: 48px;
  }
  .card {
    width: 540px; height: 309px; position: relative; overflow: hidden;
    box-shadow: 0 18px 40px rgba(0,0,0,.45);
  }
  /* Back: contact side */
  .card--back { background: var(--card-dark); }
  .card__band {
    position: absolute; inset: 0;
    background: linear-gradient(100deg, transparent 18%, var(--card-band) 34%, var(--card-band) 62%, transparent 80%);
    opacity: .8;
  }
  .brand-mark {
    position: absolute; top: 30px; right: 40px;
    display: flex; align-items: center; gap: 10px;
    color: var(--icon-blue); font-weight: 500; font-size: 15px; letter-spacing: .08em;
    text-transform: uppercase;
  }
  .brand-mark__dot {
    width: 22px; height: 22px; border-radius: 50%;
    border: 2px solid var(--icon-blue);
  }
  .person { position: absolute; left: 44px; top: 74px; }
  .person__name { font-size: 28px; line-height: 1.1; color: var(--brand-blue); }
  .person__first { font-weight: 600; }
  .person__last { font-weight: 300; }
  .person__role { margin-top: 4px; font-size: 12px; color: var(--ink-light); font-weight: 400; }
  .contacts { position: absolute; left: 44px; top: 160px; list-style: none; }
  .contacts li {
    display: flex; align-items: center; gap: 10px;
    font-size: 13px; color: var(--ink-muted); line-height: 1; margin-bottom: 9px;
  }
  .icon { width: 16px; height: 16px; flex: none; }
  .address {
    position: absolute; left: 44px; bottom: 22px;
    display: flex; align-items: center; gap: 10px;
    font-size: 13px; color: var(--brand-blue);
  }
  /* Front: brand side */
  .card--front {
    background: var(--brand-blue);
    display: flex; align-items: center; justify-content: center; gap: 16px;
  }
  .front-name {
    color: #ffffff; font-weight: 500; font-size: 30px; letter-spacing: .08em;
    text-transform: uppercase;
  }
  .front-dot {
    width: 58px; height: 58px; border-radius: 50%; border: 4px solid #ffffff;
  }
</style>
</head>
<body>
<main class="sheet">
  <section class="card card--back" aria-label="Business card back">
    <div class="card__band"></div>
    <div class="brand-mark"><span class="brand-mark__dot"></span>Meridel Health Clinic</div>
    <div class="person">
      <p class="person__name"><span class="person__first">Clara</span> <span class="person__last">Venn</span></p>
      <p class="person__role">Founder &amp; CEO</p>
    </div>
    <ul class="contacts">
      <li>
        <svg class="icon" viewBox="0 0 16 16"><circle cx="8" cy="8" r="8" fill="var(--icon-blue)"/><path d="M5.5 4.5l1.4 1.6-.8 1a5 5 0 0 0 2.8 2.8l1-.8 1.6 1.4-.8 1.2C8.3 11.6 4.4 7.7 4.3 5.3z" fill="#fff"/></svg>
        (555) 014-2280
      </li>
      <li>
        <svg class="icon" viewBox="0 0 16 16"><circle cx="8" cy="8" r="8" fill="var(--icon-blue)"/><rect x="4" y="5.2" width="8" height="5.6" rx=".6" fill="#fff"/><path d="M4.3 5.6L8 8.4l3.7-2.8" stroke="var(--icon-blue)" stroke-width=".9" fill="none"/></svg>
        hello@meridelhealth.com
      </li>
      <li>
        <svg class="icon" viewBox="0 0 16 16"><circle cx="8" cy="8" r="8" fill="var(--icon-blue)"/><circle cx="8" cy="8" r="4" fill="none" stroke="#fff" stroke-width="1"/><path d="M4 8h8M8 4c-2 2.4-2 5.6 0 8M8 4c2 2.4 2 5.6 0 8" stroke="#fff" stroke-width=".8" fill="none"/></svg>
        www.meridelhealth.com
      </li>
    </ul>
    <p class="address">
      <svg class="icon" viewBox="0 0 16 16"><circle cx="8" cy="8" r="8" fill="var(--icon-blue)"/><path d="M8 3.6a2.9 2.9 0 0 0-2.9 2.9C5.1 8.7 8 12.4 8 12.4s2.9-3.7 2.9-5.9A2.9 2.9 0 0 0 8 3.6z" fill="#fff"/><circle cx="8" cy="6.5" r="1.1" fill="var(--icon-blue)"/></svg>
      480 Linden Ave. Suite 12 Brookfield, OR 97210
    </p>
  </section>

  <section class="card card--front" aria-label="Business card front">
    <span class="front-dot"></span>
    <p class="front-name">Meridel Health Clinic</p>
  </section>
</main>
</body>
</html>
```